New website for out outstanding veterinary training center

We already have a beautiful logo with nice colors and we are now looking for a breathtaking modern website to present our training center and future corses held there. A section to book open courses should also be available.

We are planing the realize the website with Wordpress.
The following pages should be available:
- Startpage / Overview
- Page to present the different rooms and seating option
- Page where the rooms can be booked
- Page where recommended accommodation are presented
- Page to present and book corses
- contact page
- Impressum

Target Market(s)

European Union

Industry/Entity Type

Education, Veterinary medicine

Number of Pages Required

5+ page

Font styles to use
Sans Serif

Colors
00AB8E
00BBA5
67D7C9
C6EFE9
E9F9F6

Requirements
Must have
• The website must be clear and easy to read. The colors form the logos should be used for the design.
Should not have
• To playful design. The page is not for a veterinary practice. we are a training center for veterinarians!

```html
<!DOCTYPE html>
<html lang="en">
<head>
<meta charset="utf-8">
<title>Vetora Training Center – Our Courses</title>
<link href="https://fonts.googleapis.com/css2?family=Lato:wght@400;700;900&display=swap" rel="stylesheet">
<style>
:root{
  --teal:#00AB8E;
  --teal-bright:#1DB89E;
  --teal-light:#67D7C9;
  --teal-pale:#C6EFE9;
  --teal-mist:#E9F9F6;
  --teal-deep:#176864;
  --plum:#45343E;
  --footer:#463640;
  --ink:#2E2A2C;
  --white:#FFFFFF;
}
*{margin:0;padding:0;box-sizing:border-box}
html,body{width:705px;height:1200px;overflow:hidden}
body{font-family:'Lato',sans-serif;color:var(--ink);background:var(--white);position:relative}
.topbar{position:absolute;left:0;top:0;width:705px;height:34px;background:var(--teal-mist)}
.social{position:absolute;display:flex;gap:11px;align-items:center}
.social span{display:block;width:11px;height:11px;border-radius:50%}
.topbar .social{left:454px;top:12px}
.topbar .social span{background:var(--plum)}
.btn{position:absolute;display:flex;align-items:center;justify-content:center;background:var(--teal-bright);color:var(--white);font-weight:700;border-radius:20px;text-decoration:none}
.btn-top{left:576px;top:5px;width:86px;height:23px;font-size:8.5px}
.brand{position:absolute;left:44px;top:12px;width:88px;text-align:center}
.brand-mark{width:52px;height:52px;border-radius:50%;background:var(--teal-deep);margin:0 auto 3px;border:3px solid var(--white);box-shadow:0 0 0 1px var(--teal-pale)}
.brand-name{font-weight:900;font-size:15px;color:var(--plum);letter-spacing:.2px}
.nav{position:absolute;top:59px;right:43px;display:flex;gap:21px;font-size:10px;font-weight:700;color:var(--ink)}
.nav .active{color:var(--teal-bright)}
.hero{position:absolute;left:0;top:99px;width:705px;height:167px;overflow:hidden;
  background:linear-gradient(90deg,#2a3a3a 0%,#2c4a48 30%,#1f5e5a 60%,var(--teal-deep) 100%)}
.hero h1{position:absolute;right:43px;top:44px;font-size:33px;font-weight:700;color:var(--white)}
.hero svg{position:absolute;left:0;top:0}
.section-title{position:absolute;top:299px;left:0;width:705px;text-align:center;font-size:25px;font-weight:700;color:var(--plum)}
.rule{position:absolute;top:341px;left:330px;width:45px;height:2.5px;background:var(--teal-deep)}
.card{position:absolute;width:194px;text-align:center}
.card-photo{width:194px;height:118px;border-radius:6px}
.card h3{margin-top:11px;font-size:14px;font-weight:700;color:var(--plum)}
.card p{margin-top:3px;font-size:9.6px;line-height:16.3px;color:var(--ink)}
.card .btn{position:static;margin:8px auto 0;width:105px;height:32px;font-size:10.5px}
.photo-study{background:linear-gradient(135deg,#c9c2b4,#e8e2d8 50%,#b9a48f)}
.photo-dog{background:linear-gradient(135deg,#f1f1f1,#e6e3df 45%,#b5783f)}
.photo-lecture{background:linear-gradient(135deg,#b7bba9,#d8dbd0 50%,#8e8f86)}
.footer{position:absolute;left:0;top:966px;width:705px;height:234px;background:var(--footer);color:var(--white)}
.footer-brand{position:absolute;left:44px;top:56px;width:130px;text-align:center}
.footer-brand .brand-mark{width:82px;height:82px;background:transparent;border:3px solid var(--white);box-shadow:none;margin-bottom:6px}
.footer-brand .brand-name{color:var(--white);font-size:23px}
.fcol{position:absolute;top:40px;font-size:9.8px}
.fcol h4{font-size:15px;font-weight:700;color:var(--teal-bright);margin-bottom:5px}
.fcol li{list-style:none;line-height:19.5px}
.fcol p{line-height:17px;margin-bottom:3px}
.fcol .social{position:static;margin-top:12px;gap:12px}
.fcol .social span{background:var(--teal-bright);width:11px;height:11px}
.email{width:142px;height:27px;background:var(--white);border-radius:14px;color:var(--ink);font-size:9.8px;padding:0 10px;display:flex;align-items:center;margin-top:6px}
.fcol .btn{position:static;width:142px;height:27px;margin-top:8px;font-size:13px;background:var(--teal)}
</style>
</head>
<body>
<header>
  <div class="topbar">
    <div class="social" aria-label="Social links"><span></span><span></span><span></span><span></span><span></span></div>
    <a class="btn btn-top" href="#">Book Course</a>
  </div>
  <div class="brand"><div class="brand-mark"></div><div class="brand-name">Vetora</div></div>
  <nav class="nav">
    <span>Home</span><span>About Us</span><span>Rooms</span><span class="active">Book Course</span><span>Accommodation</span><span>Impressum</span><span>Contact Us</span>
  </nav>
</header>

<section class="hero" role="img" aria-label="Veterinarian gently examining a cat, teal tinted">
  <svg width="705" height="167" viewBox="0 0 705 167" aria-hidden="true">
    <path d="M0,149 C80,134 180,128 260,140 Q320,150 352,166 Q385,150 445,140 C525,128 625,134 705,147 L705,167 L0,167Z" fill="#FFFFFF"/>
  </svg>
  <h1>Our Courses</h1>
</section>

<main>
  <h2 class="section-title">Feature Courses</h2>
  <div class="rule"></div>

  <article class="card" style="left:44px;top:374px">
    <div class="card-photo photo-study" role="img" aria-label="Student studying an anatomy book beside a skeleton model"></div>
    <h3>Course Heading</h3>
    <p>Sed ut perspiciatis unde omnis iste<br>natus error sit voluptatem accusantium<br>doloremque quaerat.</p>
    <a class="btn" href="#">Book Course</a>
  </article>
  <article class="card" style="left:256px;top:374px">
    <div class="card-photo photo-dog" role="img" aria-label="Veterinarian with stethoscope holding a dog"></div>
    <h3>Course Heading</h3>
    <p>Sed ut perspiciatis unde omnis iste<br>natus error sit voluptatem accusantium<br>doloremque quaerat.</p>
    <a class="btn" href="#">Book Course</a>
  </article>
  <article class="card" style="left:468px;top:374px">
    <div class="card-photo photo-lecture" role="img" aria-label="Lecturer presenting to students beside a flip chart"></div>
    <h3>Course Heading</h3>
    <p>Sed ut perspiciatis unde omnis iste<br>natus error sit voluptatem accusantium<br>doloremque quaerat.</p>
    <a class="btn" href="#">Book Course</a>
  </article>

  <article class="card" style="left:44px;top:652px">
    <div class="card-photo photo-study" role="img" aria-label="Student studying an anatomy book beside a skeleton model"></div>
    <h3>Course Heading</h3>
    <p>Sed ut perspiciatis unde omnis iste<br>natus error sit voluptatem accusantium<br>doloremque quaerat.</p>
    <a class="btn" href="#">Book Course</a>
  </article>
  <article class="card" style="left:256px;top:652px">
    <div class="card-photo photo-dog" role="img" aria-label="Veterinarian with stethoscope holding a dog"></div>
    <h3>Course Heading</h3>
    <p>Sed ut perspiciatis unde omnis iste<br>natus error sit voluptatem accusantium<br>doloremque quaerat.</p>
    <a class="btn" href="#">Book Course</a>
  </article>
  <article class="card" style="left:468px;top:652px">
    <div class="card-photo photo-lecture" role="img" aria-label="Lecturer presenting to students beside a flip chart"></div>
    <h3>Course Heading</h3>
    <p>Sed ut perspiciatis unde omnis iste<br>natus error sit voluptatem accusantium<br>doloremque quaerat.</p>
    <a class="btn" href="#">Book Course</a>
  </article>
</main>

<footer class="footer">
  <div class="footer-brand"><div class="brand-mark"></div><div class="brand-name">Vetora</div></div>
  <div class="fcol" style="left:215px">
    <h4>Site Map</h4>
    <ul><li>Home</li><li>About Us</li><li>Rooms</li><li>Book Course</li><li>Accommodation</li><li>Impressum</li><li>Contact Us</li></ul>
  </div>
  <div class="fcol" style="left:356px">
    <h4>Contact Us</h4>
    <p>Neque porro quisquam<br>est,qui dolorem</p>
    <p style="margin-top:3px">1-800-555-0142</p>
    <p style="margin-top:4px">info@vetoraacademy.com</p>
    <div class="social" aria-label="Social links"><span></span><span></span><span></span><span></span><span></span></div>
  </div>
  <div class="fcol" style="left:521px">
    <h4>Email Subscribe</h4>
    <p style="margin-top:2px;line-height:15px">Neque porro quisquam est,<br>qui dolorem</p>
    <div class="email">Email Address</div>
    <a class="btn" href="#">Subscribe</a>
  </div>
</footer>
</body>
</html>
```